Homepage layout for online ad network

Attached is our Valtro Media logo and updated brief (I can't seem to delete the old logo and brief, but they're no longer relevant).

This project was originally posted with a different logo and corporate name, but we have decided to stay with our current logo and name and redesign the site.

Your design is for a homepage only - design, no coding (I'll get someone else to take your PSD and code it).

Your homepage will make use of a Flash slider - BUT YOU ARE NOT REQUIRED TO PROVIDE THE FLASH. Instead, simply provide the layout and at least two static examples out of the four different sections that will eventually be in the slider.

Much of this design is based on the design of a competitor (listed in the brief).

Please ask whatever questions you need to in order to clarify instructions.
Updates

Project updated to include new logo (and correspondingly new color scheme).

Brief changed slightly.

Thank you for submitting designs for this project in the past.

After some internal strategy work, we have decided to retain our initial corporate identity, Valtro Media.

If you have submitted a design for the original brief and are available, please re-work your best prior design to reflect the color scheme in the newly uploaded logo.

Target Market(s)

This site is aimed primarily at young professionals who buy digital media on behalf of large advertisers.

Industry/Entity Type

Media

Requirements
Must have
• modern white space
Should not have
• no Flash outside of slider

```html
<!DOCTYPE html>
<html lang="en">
<head>
<meta charset="utf-8">
<title>Valtro Media — Home</title>
<link rel="stylesheet" href="https://fonts.googleapis.com/css2?family=Montserrat:wght@400;500;600;700&family=Arimo:wght@400;700&family=Roboto+Condensed:wght@300;400;700&display=swap">
<style>
  :root {
    --red: #c0202f;
    --ink: #1e1e1e;
    --grey-band: #d4d4d4;
    --panel: #f8f8f8;
    --lime-light: #f1f45e;
    --lime-dark: #c9d52a;
    --slide-light: #f4f6f8;
    --slide-mid: #dde2e7;
  }
  * { margin: 0; padding: 0; box-sizing: border-box; }
  html, body { width: 1200px; height: 1000px; overflow: hidden; }
  body {
    position: relative;
    background: #fff;
    font-family: "Arimo", Arial, sans-serif;
    color: var(--ink);
  }

  /* Header */
  .site-header { position: absolute; left: 0; top: 0; width: 1200px; height: 120px; background: #fff; border-bottom: 4px solid var(--red); }
  .brand { position: absolute; left: 134px; top: 38px; display: flex; align-items: center; gap: 12px; }
  .brand-mark { width: 24px; height: 24px; background: var(--red); }
  .brand-name { font-family: "Montserrat", sans-serif; font-weight: 600; font-size: 34px; color: var(--ink); letter-spacing: -0.5px; }
  .nav-marker { position: absolute; left: 253px; top: 101px; }
  .tagline { position: absolute; right: 119px; top: 26px; font-family: "Montserrat", sans-serif; font-weight: 700; font-size: 12px; color: var(--red); letter-spacing: 0.3px; }
  .main-nav { position: absolute; right: 118px; top: 68px; display: flex; height: 33px; }
  .main-nav a { display: flex; align-items: center; padding: 0 14px; font-family: "Montserrat", sans-serif; font-weight: 700; font-size: 13px; color: var(--ink); text-decoration: none; letter-spacing: 0.3px; border-left: 1px solid #333; }
  .main-nav a:first-child { border-left: 0; }
  .main-nav a.current { border-right: 1px solid var(--red); }
  .main-nav a.current + a { border-left: 0; }
  .main-nav a:last-child { padding-right: 0; }

  .backdrop { position: absolute; left: 0; top: 120px; width: 1200px; height: 200px; background: linear-gradient(to bottom, var(--grey-band), #fff); }

  /* Slider */
  .slider { position: absolute; left: 123px; top: 150px; width: 960px; height: 351px; background: linear-gradient(100deg, var(--slide-light) 0%, var(--slide-mid) 50%, var(--slide-light) 100%); box-shadow: 0 6px 8px rgba(0,0,0,0.45); overflow: hidden; }
  .slide-photo { position: absolute; left: 505px; top: 0; width: 365px; height: 351px; background: radial-gradient(ellipse at 55% 45%, #c89a84 0%, #5a3a2c 55%, #e9eef3 100%); }
  .slide-title { position: absolute; left: 104px; top: 120px; font-family: "Montserrat", sans-serif; font-weight: 700; font-size: 40px; color: var(--red); line-height: 1; }
  .slide-sub { position: absolute; left: 105px; top: 166px; font-family: "Montserrat", sans-serif; font-weight: 500; font-size: 20.5px; line-height: 24px; color: var(--ink); letter-spacing: 0.4px; }
  .slide-arrow { position: absolute; top: 158px; }
  .slide-arrow.prev { left: 20px; }
  .slide-arrow.next { right: 16px; }
  .slider-dots { position: absolute; left: 554px; top: 516px; display: flex; gap: 13px; }
  .slider-dots span { width: 15px; height: 15px; border-radius: 50%; background: #1b1b1b; }

  /* Content */
  .content-panel { position: absolute; left: 118px; top: 658px; width: 960px; height: 248px; background: var(--panel); box-shadow: 0 8px 10px -6px rgba(0,0,0,0.35); }
  .news-column-bg { position: absolute; left: 729px; top: 545px; width: 349px; height: 361px; background: linear-gradient(to bottom, #fff 0px, #fff 113px, var(--panel) 113px); box-shadow: -6px 0 8px -6px rgba(0,0,0,0.25); }

  .about-heading { position: absolute; left: 124px; top: 566px; display: flex; align-items: center; gap: 10px; font-family: "Roboto Condensed", sans-serif; font-size: 25px; color: var(--ink); }
  .about-heading .mark { width: 22px; height: 22px; background: var(--lime-dark); }
  .about-heading b { font-weight: 700; }
  .about-heading span { font-weight: 300; }
  .about-intro { position: absolute; left: 123px; top: 608px; width: 560px; font-size: 18px; line-height: 24px; color: var(--red); }
  .about-body { position: absolute; left: 122px; top: 665px; width: 545px; font-size: 14.3px; line-height: 24.3px; color: #2a2a2a; }
  .footer-rule { position: absolute; left: 122px; top: 835px; width: 576px; border-top: 1px solid #333; }
  .quick-links { position: absolute; left: 120px; top: 854px; display: flex; }
  .quick-links a { display: flex; align-items: center; gap: 6px; font-family: "Montserrat", sans-serif; font-weight: 500; font-size: 13px; color: var(--ink); text-decoration: none; letter-spacing: 0.3px; }
  .quick-links a + a { margin-left: 22px; }
  .quick-links a.wide { margin-left: 34px; }

  .news-banner { position: absolute; left: 729px; top: 558px; width: 240px; height: 39px; background: linear-gradient(to right, var(--lime-light), var(--lime-dark) 85%, var(--lime-light)); box-shadow: 0 2px 4px rgba(0,0,0,0.35); font-family: "Roboto Condensed", sans-serif; font-size: 25px; color: var(--red); padding-left: 32px; line-height: 39px; }
  .news-list { position: absolute; left: 767px; top: 615px; width: 300px; list-style: none; }
  .news-list li { margin-bottom: 17px; font-size: 12px; line-height: 16px; color: #2a2a2a; }
  .news-list time { display: block; font-weight: 700; font-size: 12px; color: var(--red); letter-spacing: 0.4px; }

  .copyright { position: absolute; left: 0; top: 924px; width: 1246px; text-align: center; font-size: 12px; color: #222; }
</style>
</head>
<body>
  <header class="site-header">
    <div class="brand"><span class="brand-mark"></span><span class="brand-name">Valtro Media</span></div>
    <svg class="nav-marker" width="16" height="14" viewBox="0 0 16 14"><polygon points="8,0 16,14 0,14" fill="#c0202f"/></svg>
    <p class="tagline">COMPANY TAGLINE GOES HERE</p>
    <nav class="main-nav">
      <a class="current" href="#">BEAUTY</a>
      <a href="#">COOKING</a>
      <a href="#">PARENTING</a>
      <a href="#">ENTERTAINMENT</a>
      <a href="#">VIDEO</a>
      <a href="#">CPC</a>
    </nav>
  </header>

  <div class="backdrop"></div>

  <section class="slider">
    <div class="slide-photo" role="img" aria-label="Beauty campaign photo: woman with yellow flowers in her hair"></div>
    <h2 class="slide-title">BEAUTY</h2>
    <p class="slide-sub">SITE SPECIFIC CAMPAIGNS<br>AT RON PRICES</p>
    <svg class="slide-arrow prev" width="30" height="50" viewBox="0 0 30 50"><polygon points="20,0 30,0 12,25 30,50 20,50 0,25" fill="#1b1b1b"/></svg>
    <svg class="slide-arrow next" width="30" height="50" viewBox="0 0 30 50"><polygon points="10,0 0,0 18,25 0,50 10,50 30,25" fill="#1b1b1b"/></svg>
  </section>
  <div class="slider-dots"><span></span><span></span><span></span><span></span><span></span></div>

  <div class="content-panel"></div>
  <div class="news-column-bg"></div>

  <h2 class="about-heading"><span class="mark"></span><span>ABOUT</span><b>VALTRO MEDIA</b></h2>
  <p class="about-intro">Lorem ipsum dolor sit amet, consectetur adipiscing elit. Mauris dignissim nulla pharetra risus iaculis at consequat turpis vulputate.</p>
  <p class="about-body">Sed scelerisque magna ut quam scelerisque dictum. Morbi purus quam, sodales id vehicula non, ultricies vitae justo. Vivamus sed augue ut elit dapibus adipiscing vel in elit. Mauris adipiscing, elit a laoreet eleifend, orci lacus condimentum enim, vitae venenatis enim velit ac dolor. Nullam augue mauris, tincidunt et bibendum nec, consequat ut dui. Sed id ante in purus vulputate adipiscing ac non justo. Nulla libero sem, venenatis in fringilla pulvinar, ornare ac diam.</p>
  <div class="footer-rule"></div>
  <nav class="quick-links">
    <a href="#">ABOUT US <svg width="12" height="10" viewBox="0 0 12 10"><path d="M0 5H10M6 1L10 5L6 9" stroke="#c0202f" stroke-width="2" fill="none"/></svg></a>
    <a href="#">CONTACT US <svg width="12" height="10" viewBox="0 0 12 10"><path d="M0 5H10M6 1L10 5L6 9" stroke="#c0202f" stroke-width="2" fill="none"/></svg></a>
    <a class="wide" href="#">MANAGEMENT TEAM <svg width="12" height="10" viewBox="0 0 12 10"><path d="M0 5H10M6 1L10 5L6 9" stroke="#c0202f" stroke-width="2" fill="none"/></svg></a>
    <a href="#">NEWS <svg width="12" height="10" viewBox="0 0 12 10"><path d="M0 5H10M6 1L10 5L6 9" stroke="#c0202f" stroke-width="2" fill="none"/></svg></a>
    <a href="#">CAREERS <svg width="12" height="10" viewBox="0 0 12 10"><path d="M0 5H10M6 1L10 5L6 9" stroke="#c0202f" stroke-width="2" fill="none"/></svg></a>
  </nav>

  <h2 class="news-banner">VALTRO NEWS</h2>
  <ul class="news-list">
    <li><time>JANUARY 15, 2011</time>Valtro Media&nbsp; unveils new web site design and digital strategy</li>
    <li><time>DECEMBER 22, 2010</time>Valtro Media featured in Foundermag.com as one<br>of the fastest grown online ad agencies.</li>
    <li><time>NOVEMBER 15, 2010</time>As RTB Goes Mainstream, Display Services Try To<br>Pull Publishers Along</li>
    <li><time>NOVEMBER 9, 2010</time>Morbi purus quam, sodales id vehicula non, ultricies vitae justo</li>
  </ul>

  <footer class="copyright">Copyright 2011 Valtro Media. All Rights Reserved</footer>
</body>
</html>
```